Salon and Spa Distributor Business Card

Need a business card. We are are distributor in the salon and spa industry. We identify with natural beauty. Need a card with:
Company Name: Petal Quarry"
Title: "President & CEO"
Address
Company Phone number
email
website
Tag Line:" The Professional Salon Source"

Industry/Entity Type

Business

Contact Information for Business Card

Name: Dov Strommen
Title: "President & CEO"
Address: 31 Harlow Ln, Bexmoor, NJ 07813
Company Phone number: 800-463-5918
email: dovstrommen@petalquarry.example
website: www.petalquarry.example

Requirements
Should not have
• No black backgrounds

```html
<!DOCTYPE html>
<html lang="en">
<head>
<meta charset="utf-8">
<title>Petal Quarry – Business Card</title>
<link href="https://fonts.googleapis.com/css2?family=Questrial&family=Lato:wght@400&display=swap" rel="stylesheet">
<style>
  :root {
    --stage: #000000;
    --paper: #f9f9f9;
    --green: #3a8f3f;
    --green-light: #3b8d43;
    --green-dark: #0d6a35;
    --ink: #111111;
    --white: #ffffff;
  }
  html, body {
    margin: 0;
    width: 1200px;
    height: 900px;
    overflow: hidden;
    background: var(--stage);
  }
  .card {
    position: absolute;
    top: 271px;
    width: 457px;
    height: 281px;
    border-radius: 12px;
    overflow: hidden;
  }
  .card--front { left: 137px; background: var(--paper); }
  .card--back {
    left: 626px;
    background: linear-gradient(180deg, var(--green-light) 0%, var(--green-dark) 100%);
  }

  .brand-mark {
    position: absolute;
    border-radius: 50%;
  }
  .card--front .brand-mark {
    left: 84px; top: 56px; width: 76px; height: 76px;
    background: var(--green);
  }
  .card--back .brand-mark {
    left: 78px; top: 90px; width: 96px; height: 96px;
    background: var(--white);
  }
  .brand-name {
    position: absolute;
    margin: 0;
    font-family: "Questrial", sans-serif;
    font-weight: 400;
    white-space: nowrap;
  }
  .card--front .brand-name {
    left: 32px; top: 160px;
    font-size: 28px;
    color: var(--green);
  }
  .card--back .brand-name {
    left: 196px; top: 122px;
    font-size: 28px;
    color: var(--white);
  }

  .contact {
    position: absolute;
    left: 238px;
    top: 38px;
    font-family: "Lato", sans-serif;
    color: var(--ink);
  }
  .contact__name {
    margin: 0;
    font-family: "Questrial", sans-serif;
    font-size: 22px;
    letter-spacing: 0.5px;
    color: var(--green);
    line-height: 26px;
  }
  .contact__title {
    margin: 1px 0 0;
    font-size: 12px;
    line-height: 16px;
  }
  .contact__list {
    list-style: none;
    margin: 20px 0 0;
    padding: 0;
    font-size: 12.5px;
    line-height: 16.5px;
  }
  .contact__list li { display: flex; align-items: center; }
  .contact__list svg { width: 10px; height: 10px; margin-right: 6px; fill: var(--green); flex: none; }
  .contact__address {
    margin: 15px 0 0;
    font-style: normal;
    font-size: 12.5px;
    line-height: 17px;
  }

  .tagline-band {
    position: absolute;
    left: 0; bottom: 0;
    width: 100%;
    height: 64px;
    background: linear-gradient(180deg, var(--green-light) 0%, var(--green-dark) 100%);
    display: flex;
    align-items: center;
    justify-content: center;
  }
  .tagline {
    margin: 0;
    font-family: "Lato", sans-serif;
    font-size: 14px;
    letter-spacing: 0.3px;
    color: var(--white);
    text-transform: uppercase;
  }
</style>
</head>
<body>

<section class="card card--front">
  <span class="brand-mark" aria-hidden="true"></span>
  <p class="brand-name">Petal Quarry</p>

  <div class="contact">
    <h1 class="contact__name">DOV STROMMEN</h1>
    <p class="contact__title">President &amp; CEO</p>
    <ul class="contact__list">
      <li>
        <svg viewBox="0 0 10 10" aria-hidden="true"><path d="M1 3.2C1 2 2.2 1.5 5 1.5S9 2 9 3.2V4H7V3H3v1H1z M2 5h6l1 3.5H1z"/></svg>
        800-463-5918
      </li>
      <li>
        <svg viewBox="0 0 10 10" aria-hidden="true"><path d="M0.5 2h9v6h-9z M1 2.4L5 5.6 9 2.4" stroke="#fff" stroke-width="0.8"/></svg>
        dovstrommen@petalquarry.example
      </li>
      <li>
        <svg viewBox="0 0 10 10" aria-hidden="true"><circle cx="5" cy="5" r="4.6"/><path d="M0.6 5h8.8M5 0.4v9.2M5 0.4C2.8 3 2.8 7 5 9.6M5 0.4C7.2 3 7.2 7 5 9.6" stroke="#fff" stroke-width="0.6" fill="none"/></svg>
        www.petalquarry.example
      </li>
    </ul>
    <address class="contact__address">31 Harlow Ln,<br>Bexmoor, NJ 07813</address>
  </div>

  <div class="tagline-band">
    <p class="tagline">The Professional Salon Source</p>
  </div>
</section>

<section class="card card--back">
  <span class="brand-mark" aria-hidden="true"></span>
  <p class="brand-name">Petal Quarry</p>
</section>

</body>
</html>
```